Media Services Start-up -- Corporate Website and Logo Design. Inspiration required!

We need a logo design and corporate website design, including coding, for our start-up business.
Vennatra’s value proposition is based on bringing together media content from a vast number of geographies globally, adding human and AI curation, translation and editing, and delivering the content using tailored customer interfaces. On the one hand, the business brings together media coverage from all over the world, and on the other it brings together content, human skills and technology to deliver a supreme customer experience.
Vennatra is a B2B media monitoring and analytics business with emphasis on global customers. Vennatra's service offering is centred around sourcing media content from different markets, processing, storing and delivering the content and insights derived from it using an online platform / mobile app.
The messaging we want to create through the logo is:
- Global scope
- Speed of delivery
- Cost-efficiency
- Multi-lingual
- Tailor-made
- Trustworthy
Target Market(s)
Business to business, PR / Communications, Media, Marketing
Logo Text
Vennatra
Coding
Coded - Design and coding required
Number of Pages Required
5+ page
Font styles to use
Other font styles liked:
- See Design Brief for details
Colors
Designer to choose colors to be used in the design.

```html
<!DOCTYPE html>
<html lang="en">
<head>
<meta charset="utf-8">
<title>Vennatra — Global Media Intelligence</title>
<link rel="stylesheet" href="https://fonts.googleapis.com/css2?family=Roboto:wght@400;500;700;900&family=Arimo:wght@400&display=swap">
<style>
  :root {
    --ink: #000000;
    --paper: #ffffff;
    --hero-deep: #1c1d22;
    --hero-mid: #3a3b42;
    --hero-warm: #5a4a44;
    --field-border: #3b3b3b;
    --placeholder: #6a6a6a;
    --footer-text: #111111;
  }
  * { box-sizing: border-box; margin: 0; padding: 0; }
  html, body { width: 1200px; height: 747px; overflow: hidden; background: var(--paper); }
  body { position: relative; font-family: "Roboto", sans-serif; color: var(--ink); }

  .site-header { position: absolute; left: 0; top: 0; width: 1200px; height: 71px; background: var(--paper); z-index: 2; }
  .brand { position: absolute; left: 143px; top: 16px; font-size: 29px; font-weight: 700; letter-spacing: -0.2px; }
  .main-nav a { position: absolute; top: 26px; font-size: 14px; color: var(--ink); text-decoration: none; }
  .sign-in { position: absolute; left: 967px; top: 18px; width: 92px; height: 35px; background: var(--ink); color: var(--paper);
             border-radius: 3px; font-size: 15px; display: flex; align-items: center; justify-content: center;
             box-shadow: 0 3px 8px rgba(0,0,0,.25); }

  .hero-bg { position: absolute; left: 0; top: 71px; }

  .hero-copy { position: absolute; left: 140px; top: 268px; color: var(--paper); }
  .hero-title { font-size: 37px; font-weight: 700; line-height: 58px; letter-spacing: .3px; text-shadow: 0 3px 4px rgba(0,0,0,.6); }
  .hero-lead { margin-top: 24px; margin-left: 2px; width: 460px; font-family: "Arimo", sans-serif; font-size: 15.6px; line-height: 25.4px; }

  .lead-card { position: absolute; left: 766px; top: 214px; width: 293px; height: 337px; background: var(--paper); border-radius: 6px; }
  .lead-card svg { position: absolute; left: 3px; top: 3px; }
  .lead-card h2 { position: absolute; left: 0; top: 19px; width: 100%; text-align: center; color: var(--paper); font-size: 17px; font-weight: 500; }
  .field { position: absolute; left: 32px; width: 228px; height: 37px; border: 1px solid var(--field-border); border-radius: 3px;
           font-size: 12.5px; color: var(--placeholder); padding-left: 13px; display: flex; align-items: center; }
  .cta { position: absolute; left: 57px; top: 268px; width: 178px; height: 35px; background: var(--ink); color: var(--paper);
         border-radius: 2px; font-size: 15px; display: flex; align-items: center; justify-content: center; }

  .site-footer { position: absolute; left: 0; top: 712px; width: 1200px; height: 35px; }
  .copyright { position: absolute; left: 142px; top: 6px; font-size: 12.3px; color: var(--footer-text); }
  .social { position: absolute; left: 951px; top: 3px; display: flex; gap: 6px; }
  .social span { width: 22px; height: 22px; border-radius: 50%; background: var(--ink); display: block; }
</style>
</head>
<body>
  <header class="site-header">
    <div class="brand">Vennatra</div>
    <nav class="main-nav">
      <a style="left:363px">Home</a>
      <a style="left:454px">Solutions</a>
      <a style="left:568px">How We Do It</a>
      <a style="left:707px">Our People</a>
      <a style="left:829px">Our Technology</a>
    </nav>
    <div class="sign-in">SIGN IN</div>
  </header>

  <svg class="hero-bg" width="1200" height="640" viewBox="0 0 1200 640" role="img" aria-label="Photo of a hand writing with a fountain pen over printed charts and analytics reports">
    <defs>
      <linearGradient id="heroShade" x1="0" y1="0" x2="1" y2="1">
        <stop offset="0" stop-color="var(--hero-warm)"/>
        <stop offset=".45" stop-color="var(--hero-mid)"/>
        <stop offset="1" stop-color="var(--hero-deep)"/>
      </linearGradient>
    </defs>
    <path d="M0 0 H1200 V557 Q600 719 0 557 Z" fill="url(#heroShade)"/>
  </svg>

  <section class="hero-copy">
    <h1 class="hero-title">DELIVERING GLOBAL MEDIA<br>INTELLIGENCE</h1>
    <p class="hero-lead">Vennatra is an international media intelligence service provider. We help communications teams builds and operate truly global media monitoring and measurement programmes.</p>
  </section>

  <aside class="lead-card">
    <svg width="287" height="60" viewBox="0 0 287 60" aria-hidden="true">
      <path d="M0 6 Q0 0 6 0 H281 Q287 0 287 6 V39 Q143 78 0 39 Z" fill="var(--ink)"/>
    </svg>
    <h2>Learn More About Vennatra</h2>
    <div class="field" style="top:88px">Name</div>
    <div class="field" style="top:145px">Email Address</div>
    <div class="field" style="top:201px">Phone</div>
    <div class="cta">GET STARTED</div>
  </aside>

  <footer class="site-footer">
    <p class="copyright">© 2019 Vennatra Analytics Media. All rights reserved.</p>
    <div class="social" aria-label="Social links"><span></span><span></span><span></span><span></span></div>
  </footer>
</body>
</html>
```